The Velvet Magpie business card

I need a business card for my makeup artist business. I specialise in bridal, glamour, formal and special occasion makeup.
I am a mobile makeup artist who caters for every from nowra to sydney.
I do the following services:
Bridal makeup
airbrush makeup
special occasion
formals
hens nights/ girls night
makeup lesson
makeup for all ages from flower girl to Nanna of the bride!
photoshoot makeup
SPFX

I would like the card to portray a very professional sleek makeup business. I would also like another version of the card directed especially towards brides.

Please see my website to understand colours etc www.thevelvetmagpie-example.com

The Velvet Magpie
Professional Makeup Artist
Lorraine Kedby
0491802643
info@thevelvetmagpie-example.com
www.thevelvetmagpie-example.com
www.facebook.com/thevelvetmagpie

```html
<!DOCTYPE html>
<html lang="en">
<head>
<meta charset="utf-8">
<title>The Velvet Magpie – Business Card</title>
<link rel="stylesheet" href="https://fonts.googleapis.com/css2?family=Oswald:wght@300;400;700&family=Open+Sans:wght@400;700&display=swap">
<style>
  :root {
    --pink: #e01c8c;
    --pink-deep: #c8137a;
    --grey-dark: #4a4a4a;
    --grey-mid: #8c8c8c;
    --grey-light: #d9d9d9;
    --grey-faint: #efefef;
    --ink: #222;
    --white: #ffffff;
    --backdrop: #ececec;
  }
  * { box-sizing: border-box; margin: 0; padding: 0; }
  html, body { width: 1200px; height: 913px; overflow: hidden; }
  body { background: var(--backdrop); position: relative; font-family: "Oswald", sans-serif; }

  .card {
    position: absolute;
    width: 560px; height: 320px;
    overflow: hidden;
    box-shadow: 0 6px 18px rgba(0,0,0,.18);
    background: var(--white);
  }
  .card--front { left: 50px; top: 130px; }
  .card--back { left: 590px; top: 460px; }

  .card__art { position: absolute; inset: 0; width: 100%; height: 100%; }

  /* Front */
  .brand {
    position: absolute; left: 30px; top: 68px;
    font-family: "Oswald", sans-serif; font-weight: 400;
    font-size: 44px; letter-spacing: 4px; color: var(--pink);
    text-transform: uppercase; line-height: 1;
  }
  .contact { position: absolute; left: 32px; top: 170px; list-style: none; }
  .contact__item {
    display: flex; align-items: center; gap: 8px;
    font-size: 15px; font-weight: 400; color: var(--ink);
    height: 24px;
  }
  .contact__icon { width: 14px; height: 14px; flex: none; }
  .contact__square { width: 12px; height: 12px; background: var(--pink); flex: none; margin: 0 1px; }

  .person {
    position: absolute; right: 22px; top: 206px;
    color: var(--white); font-family: "Open Sans", sans-serif;
  }
  .person__name { font-weight: 700; font-size: 21px; line-height: 1.25; white-space: nowrap; }
  .person__role { font-family: "Oswald", sans-serif; font-weight: 300; font-size: 15px; letter-spacing: .3px; white-space: nowrap; }

  /* Back */
  .photo {
    position: absolute; inset: 0;
    background: linear-gradient(160deg, #3b3a3f 0%, #5a5470 35%, #3e45a0 60%, #e7d6c8 85%, #f1efe6 100%);
  }
  .services {
    position: absolute; left: 0; right: 0; bottom: 0; height: 122px;
    background: linear-gradient(90deg, rgba(224,28,140,.95), rgba(200,19,122,.85));
    display: flex; flex-direction: column; justify-content: center; align-items: center;
    padding: 0 14px;
  }
  .services__line {
    font-family: "Oswald", sans-serif; font-weight: 700;
    font-size: 15.5px; color: var(--white); line-height: 1.55;
    white-space: nowrap; letter-spacing: .2px;
  }
</style>
</head>
<body>

<section class="card card--front" aria-label="Business card front">
  <svg class="card__art" viewBox="0 0 560 320" aria-hidden="true">
    <ellipse cx="480" cy="18" rx="85" ry="42" fill="var(--grey-faint)"/>
    <path d="M560,70 C480,80 430,130 380,190 C320,265 220,305 60,320 L560,320 Z" fill="var(--pink)"/>
    <path d="M560,58 C478,68 426,116 374,178 C314,252 214,292 54,308" fill="none" stroke="var(--grey-dark)" stroke-width="10"/>
    <path d="M552,42 C472,56 420,102 366,164 C306,236 206,278 40,294" fill="none" stroke="var(--grey-mid)" stroke-width="4"/>
    <path d="M540,30 C466,46 416,90 360,152" fill="none" stroke="var(--grey-light)" stroke-width="3"/>
  </svg>

  <div class="brand">The Velvet Magpie</div>

  <ul class="contact">
    <li class="contact__item">
      <svg class="contact__icon" viewBox="0 0 16 16"><path d="M4 1l3 3-2 2c1 2 3 4 5 5l2-2 3 3-2 3C7 15 1 9 1 3z" fill="var(--pink)"/></svg>
      0491802643
    </li>
    <li class="contact__item">
      <svg class="contact__icon" viewBox="0 0 16 16"><rect x="1" y="3" width="14" height="10" fill="var(--pink)"/><path d="M1 3l7 6 7-6" fill="none" stroke="#fff" stroke-width="1.4"/></svg>
      info@thevelvetmagpie-example.com
    </li>
    <li class="contact__item">
      <svg class="contact__icon" viewBox="0 0 16 16"><circle cx="8" cy="8" r="7" fill="var(--pink)"/><path d="M1 8h14M8 1c-3 4-3 10 0 14M8 1c3 4 3 10 0 14" fill="none" stroke="#fff" stroke-width="1"/></svg>
      www.thevelvetmagpie-example.com
    </li>
    <li class="contact__item">
      <span class="contact__square"></span>
      /thevelvetmagpie
    </li>
  </ul>

  <div class="person">
    <p class="person__name">Lorraine Kedby</p>
    <p class="person__role">Professional Makeup Artist</p>
  </div>
</section>

<section class="card card--back" aria-label="Business card back">
  <div class="photo" role="img" aria-label="Photo of five bridesmaids in blue lace dresses holding white and green bouquets"></div>
  <div class="services">
    <p class="services__line">Bridal makeup • Airbrush makeup • Special occasion • Formals</p>
    <p class="services__line">• Hens nights/ Girls night • Makeup lesson • Makeup for all ages from flower</p>
    <p class="services__line">girl to Nanna of the bride! • Photoshoot makeup • SPFX</p>
  </div>
</section>

</body>
</html>
```